Tellmora Corporate Stationery

Look for design of all new corporate stationery for an existing insurance broking business that is going through a redesign and move from older partners to younger family members. New Logo is attached. Company is Brisbane based.
Colours in the Logo is Hex #43bed8 and website features a lot of hex #17b8d8. Website front page "A plan to protect you" - headline. "Professional and Individual advice to protect your greatest assets" - tagline.

Stationery required: Business Cards, Letter head, Thank-you cards, Birthday cards, Presentation folders, With Compliment slips and a powerpoint template. We also would like to send a card to all customers with the something along of the lines of "something new".

Target Market(s)

Customers of Insurance business looking at superannuation, life and income protection insurance, investment advice and wills

Industry/Entity Type

Insurance Broker

Font styles to use
Other font styles liked:
• same as logo

Requirements
Must have
• The above designs for new stationery for the new business including:
• Business Cards, Letter head, Thank-you cards, Birthday cards, Presentation folders, With Compliment slips and a powerpoint template. We also would like to send a card to all customers with the something along of the lines of "something new".
Nice to have
• It is a new look - long time family business being passed to next generation - big focus on advice for YOU, individual advice etc..

```html
<!DOCTYPE html>
<html lang="en">
<head>
<meta charset="utf-8">
<title>Tellmora Financial Group – Letterhead</title>
<link href="https://fonts.googleapis.com/css2?family=Questrial&display=swap" rel="stylesheet">
<style>
  :root{
    --brand-blue:#17b8d8;
    --brand-teal:#43bed8;
    --ink-grey:#6d7275;
    --bar-grey:#8f9396;
    --wash:#e3f4f7;
    --wash-deep:#d3edf2;
    --backdrop:#cdebef;
    --paper:#ffffff;
  }
  *{margin:0;padding:0;box-sizing:border-box}
  html,body{width:1200px;height:784px;overflow:hidden}
  body{background:var(--backdrop);font-family:"Questrial",sans-serif;position:relative}
  .letterhead{
    position:absolute;left:338px;top:22px;width:524px;height:740px;
    background:radial-gradient(ellipse at 55% 45%,var(--paper) 40%,#f3fafb 100%);
    box-shadow:0 6px 18px rgba(40,110,125,.18);
    overflow:hidden;
  }
  .corner-wash{
    position:absolute;left:0;bottom:0;width:524px;height:330px;
    background:linear-gradient(20deg,var(--wash-deep) 0%,var(--wash) 35%,rgba(255,255,255,0) 70%);
  }
  .brand{position:absolute;left:34px;top:34px;display:flex;align-items:center;gap:8px}
  .brand-dot{width:16px;height:16px;border-radius:50%;background:var(--ink-grey)}
  .brand-name{font-size:22px;letter-spacing:2px;color:var(--brand-blue)}
  .contact{
    position:absolute;right:30px;top:228px;width:190px;padding:10px 0 10px 12px;
    border-left:2px solid var(--wash-deep);
    font-style:normal;font-size:7.5px;color:var(--ink-grey);line-height:12px
  }
  .contact-title{color:var(--brand-blue);font-size:9px;letter-spacing:.6px;margin-bottom:3px}
  .contact-line{display:flex;align-items:center;gap:5px;white-space:nowrap}
  .contact-line svg{width:8px;height:8px;flex:none}
  .tagline{
    position:absolute;left:30px;right:30px;bottom:28px;white-space:nowrap;
    font-size:8.5px;letter-spacing:.8px;color:var(--brand-blue);text-transform:uppercase
  }
  .footer-bar{position:absolute;left:0;bottom:12px;height:8px;width:390px;background:var(--brand-blue)}
  .footer-bar-grey{position:absolute;left:396px;bottom:12px;height:8px;width:128px;background:linear-gradient(90deg,#c9cccd,var(--bar-grey))}
</style>
</head>
<body>
  <main class="letterhead">
    <div class="corner-wash" role="img" aria-label="Soft pale blue wash across the lower corner of the sheet"></div>

    <div class="brand">
      <span class="brand-dot"></span>
      <span class="brand-name">TELLMORA</span>
    </div>

    <address class="contact">
      <div class="contact-title">TELLMORA FINANCIAL GROUP</div>
      <div class="contact-line">
        <svg viewBox="0 0 10 10"><circle cx="5" cy="5" r="5" fill="var(--ink-grey)"/><path d="M5 2.2a1.8 1.8 0 0 1 1.8 1.8C6.8 5.4 5 7.8 5 7.8S3.2 5.4 3.2 4A1.8 1.8 0 0 1 5 2.2z" fill="#fff"/></svg>
        48 Harbour Street, Suite 200 Brisbane QLD 4000
      </div>
      <div class="contact-line">
        <svg viewBox="0 0 10 10"><circle cx="5" cy="5" r="5" fill="var(--ink-grey)"/><path d="M3.3 2.5l1 1-.6.8c.4.8 1 1.4 1.8 1.8l.8-.6 1 1-.6.9C4.8 7.2 2.8 5.2 2.6 3.1z" fill="#fff"/></svg>
        (07) 3000 4120
      </div>
      <div class="contact-line">
        <svg viewBox="0 0 10 10"><circle cx="5" cy="5" r="5" fill="var(--ink-grey)"/><rect x="3" y="2.8" width="4" height="4.4" rx=".5" fill="#fff"/></svg>
        (07) 3000 4121
      </div>
      <div class="contact-line">
        <svg viewBox="0 0 10 10"><circle cx="5" cy="5" r="5" fill="var(--ink-grey)"/><circle cx="5" cy="5" r="2.4" fill="none" stroke="#fff" stroke-width=".8"/></svg>
        www.tellmorafinancial.com
      </div>
    </address>

    <p class="tagline">Advice shaped around you – personal guidance for what matters most</p>
    <div class="footer-bar"></div>
    <div class="footer-bar-grey"></div>
  </main>
</body>
</html>
```